Visitenkarten-Design
Zielgruppe
Zielgruppe sind Großhändler in der Elektrotechnik, Fachfirmen für Notbeleuchtung. Produkte: Notbeleuchtungssysteme, Not- und Sicherheitsleuchten, Akkumulatoren/Batterien (industrielle)
Aufgabenstellung
Optimale Darstellung des Logos und der Werte des Unternehmens. Einhaltung der Farben des Logos. Eher eine helle Businesskarte, nicht zu Dunkel.
Wir bitten, dass uns der Gewinner gleich für die ersten 6 Mitarbeiter, welche Visitenkarten in unserem Unternehmen benötigen, zu erstellen.
Die bestehende Visitenkarte kam leider nicht gut an. Falsche Farben und kein komplett abgestimmtes Design.
Die neue Visitenkarte soll gut zur Website passen und die Firma optimal repräsentieren.
!Bitte nicht die Farbe der bestehenden Visitenkarte benutzen sondern nur Farbtöne des Logos. Bitte nicht zwingend am bestehenden Design der Visitenkarte orientieren, wir möchten frische Ideen!

```html
<!DOCTYPE html>
<html lang="de">
<head>
<meta charset="utf-8">
<title>Visitenkarte – Lumavo</title>
<link rel="stylesheet" href="https://fonts.googleapis.com/css2?family=Outfit:wght@400;500;700&family=Doto:wght@900&display=swap">
<style>
  :root {
    --magenta: #a3114c;
    --pink-soft: #eac2d6;
    --pink-mist: #f6e3ec;
    --ink: #3a3f47;
    --paper: #ffffff;
    --stage: #ececee;
  }
  * { box-sizing: border-box; margin: 0; padding: 0; }
  html, body {
    width: 1200px; height: 1200px; overflow: hidden;
    background: var(--stage);
    font-family: "Outfit", sans-serif;
  }
  .business-card {
    position: absolute; left: 100px; top: 280px;
    width: 1000px; height: 640px; overflow: hidden;
    background:
      radial-gradient(ellipse 520px 360px at 22% 22%, var(--pink-soft) 0%, rgba(234,194,214,0) 70%),
      radial-gradient(ellipse 480px 320px at 92% 72%, var(--pink-soft) 0%, rgba(234,194,214,0) 72%),
      radial-gradient(ellipse 420px 260px at 50% 100%, var(--pink-mist) 0%, rgba(246,227,236,0) 70%),
      var(--paper);
  }
  .holder { position: absolute; left: 96px; top: 88px; }
  .holder-name {
    font-weight: 700; font-size: 46px; color: var(--magenta);
    letter-spacing: -0.5px; line-height: 1;
  }
  .holder-role {
    margin-top: 10px; font-size: 21px; font-style: italic;
    color: var(--magenta); line-height: 1.1;
  }
  .company-mark {
    position: absolute; left: 612px; top: 88px;
    display: flex; align-items: center; gap: 22px;
  }
  .company-mark .square {
    width: 104px; height: 104px; border: 6px solid var(--ink);
  }
  .company-mark .wordmark {
    font-weight: 500; font-size: 36px; color: var(--ink); letter-spacing: 2px;
  }
  .contact-list {
    position: absolute; left: 100px; top: 390px; list-style: none;
  }
  .contact-list li {
    display: flex; align-items: center; gap: 26px;
    font-size: 22px; color: var(--ink); height: 50px;
  }
  .contact-list svg { width: 30px; height: 30px; flex: none; }
  .company-address {
    position: absolute; left: 630px; top: 380px;
    font-style: normal; font-size: 31px; line-height: 42px; color: var(--ink);
  }
  .web-address {
    position: absolute; left: 0; right: 0; bottom: -14px;
    font-family: "Doto", monospace; font-weight: 900;
    font-size: 78px; letter-spacing: 4px; color: var(--magenta);
    white-space: nowrap; text-align: center; line-height: 1;
  }
</style>
</head>
<body>
  <article class="business-card">
    <header class="holder">
      <h1 class="holder-name">Mirko Selbert</h1>
      <p class="holder-role">Geschäftsführer<br>Managing Director</p>
    </header>

    <div class="company-mark">
      <span class="square"></span>
      <span class="wordmark">LUMAVO</span>
    </div>

    <ul class="contact-list">
      <li>
        <svg viewBox="0 0 30 30" aria-hidden="true"><circle cx="15" cy="15" r="15" fill="#3a3f47"/><path d="M10 8.5c1-.6 1.8 0 2.4 1.2l.8 1.8c.3.8 0 1.4-.7 1.9-.4.3-.4.7-.2 1.1.9 1.6 2 2.7 3.5 3.5.4.2.8.2 1.1-.2.5-.7 1.1-1 1.9-.7l1.8.8c1.2.6 1.8 1.4 1.2 2.4-.8 1.4-2.4 2.1-4 1.6-4.2-1.3-7.5-4.6-8.8-8.8-.5-1.6.2-3.2 1-4.6z" fill="#fff"/></svg>
        <span>08731 40217 63</span>
      </li>
      <li>
        <svg viewBox="0 0 30 30" aria-hidden="true"><circle cx="15" cy="15" r="15" fill="#3a3f47"/><path d="M10 8.5c1-.6 1.8 0 2.4 1.2l.8 1.8c.3.8 0 1.4-.7 1.9-.4.3-.4.7-.2 1.1.9 1.6 2 2.7 3.5 3.5.4.2.8.2 1.1-.2.5-.7 1.1-1 1.9-.7l1.8.8c1.2.6 1.8 1.4 1.2 2.4-.8 1.4-2.4 2.1-4 1.6-4.2-1.3-7.5-4.6-8.8-8.8-.5-1.6.2-3.2 1-4.6z" fill="#fff"/></svg>
        <span>0176-3829154</span>
      </li>
      <li>
        <svg viewBox="0 0 30 30" aria-hidden="true"><circle cx="15" cy="15" r="15" fill="#3a3f47"/><rect x="8" y="10" width="14" height="10" rx="1.5" fill="none" stroke="#fff" stroke-width="1.8"/><path d="M8.5 11l6.5 5 6.5-5" fill="none" stroke="#fff" stroke-width="1.8"/></svg>
        <span>mirko.selbert@lumavo.com</span>
      </li>
    </ul>

    <address class="company-address">
      Lumavo GmbH<br>
      Lindenweg 4<br>
      D-84512 Altmarkt
    </address>

    <p class="web-address">WWW.LUMAVO.COM</p>
  </article>
</body>
</html>
```